Trading journal (Ledger Pulse)

I need a design for trading journal application.
I would like to start from dark version of the design and the main goal that it should be pretty intuitive for everyone. I am going to create the app from scratch and I don't have any logo or branding colors, so it is up to you to choose a color scheme but it is a dark mode, so one of the colors would be black obviously.
The app will be available for web PC, Android and iOS.

There is google document with the requirements.
https://files.morvaly.net/page/d/7KpLsW2vQeR9tY4uZ1aBcD3fG5hJ8nM0xZ6oIqEw/view?mode=share

Target Market(s)

Professional traders

Industry/Entity Type

Trading

Colors

Designer to choose colors to be used in the design.

Requirements
Must have
• Dark mode design for PC and mobile views, the design must be pretty intuitive for everyone.
Nice to have
• Tooltips for something non obvious; popovers after completing some actions

```html
<!DOCTYPE html>
<html lang="en">
<head>
<meta charset="utf-8">
<title>Ledger Pulse – Dashboard</title>
<link href="https://fonts.googleapis.com/css2?family=Roboto:ital,wght@0,300;0,400;0,500;0,700;1,400&display=swap" rel="stylesheet">
<style>
:root{
  --bg:#202327;
  --sidebar:#1b1d21;
  --panel:#25282d;
  --card:#2a2d32;
  --cell:#2f3237;
  --grid:#33363c;
  --text:#ffffff;
  --muted:#8a93a3;
  --soft:#c9ced6;
  --accent:#5b8ff5;
  --green:#2ccb97;
  --green-dark:#1f7e63;
  --line:#27e02a;
  --red:#ef4444;
  --blue:#6699f0;
  --yellow:#f5c518;
  --purple:#b43be8;
}
*{box-sizing:border-box;margin:0;padding:0}
html,body{width:1200px;height:871px;overflow:hidden;background:var(--bg);font-family:'Roboto',sans-serif;color:var(--text)}
.app{position:relative;width:1200px;height:871px}
.sidebar{position:absolute;left:0;top:0;width:68px;height:871px;background:var(--sidebar)}
.avatar{position:absolute;left:17px;top:24px;width:34px;height:34px;border-radius:50%;background:#e9e9e9}
.avatar::after{content:"";position:absolute;right:1px;top:5px;width:7px;height:7px;border-radius:50%;background:var(--green);border:1.5px solid #e9e9e9}
.nav-active{position:absolute;left:0;top:255px;width:76px;height:59px;background:var(--accent);border-radius:0 4px 4px 0;display:flex;align-items:center;justify-content:center}
.nav-icon{position:absolute;left:22px;width:24px;height:24px}
.nav-sep{position:absolute;left:26px;width:16px;height:1px;background:#3a3d43}
.fab{position:absolute;left:19px;top:817px;width:33px;height:33px;border-radius:50%;background:var(--green);display:flex;align-items:center;justify-content:center;font-size:22px;font-weight:300}
.greeting{position:absolute;left:103px;top:26px;font-size:16px}
.title{position:absolute;left:103px;top:46px;font-size:31px;font-weight:400}
.title small{font-size:12px;margin-left:4px}
.filter{position:absolute;left:794px;top:59px;font-size:12px;color:var(--muted)}
.filter-btn{position:absolute;left:858px;top:42px;width:33px;height:34px;border-radius:4px;background:#3a3e45;display:flex;align-items:center;justify-content:center}
.chart-card{position:absolute;left:103px;top:92px;width:787px;height:314px;background:var(--card);border-radius:4px}
.chart-title{position:absolute;left:24px;top:32px;font-size:17px}
.range{position:absolute;right:24px;top:35px;font-size:12px;color:var(--muted)}
.range b{color:var(--text);font-weight:400}
.axis{position:absolute;top:272px;font-size:12px;color:var(--muted);transform:translateX(-50%)}
.tooltip{position:absolute;left:397px;top:77px;width:66px;height:34px;background:#1f2125;border-radius:3px;font-size:12px;font-weight:700;display:flex;align-items:center;justify-content:center}
.stat{position:absolute;width:240px;height:128px;border-radius:8px;background:var(--green)}
.stat.red{background:var(--red)}
.stat.blue{background:var(--blue)}
.stat .value{position:absolute;left:26px;top:20px;font-size:31px;font-weight:400}
.stat .label{position:absolute;left:25px;top:74px;font-size:14px}
.stat .sub{position:absolute;left:25px;top:92px;font-size:11.5px;color:rgba(255,255,255,.8);display:flex;align-items:center;gap:6px}
.stat .dot{width:13px;height:13px;border-radius:50%;background:rgba(0,0,0,.22)}
.stat .icon{position:absolute;right:20px;top:16px;width:40px;height:40px;border-radius:50%;background:rgba(0,0,0,.35);display:flex;align-items:center;justify-content:center}
.stat.blue .icon{background:rgba(30,50,100,.55)}
.stat.red .icon{background:rgba(120,20,20,.45)}
.add-tile{position:absolute;left:103px;top:726px;width:241px;height:128px;border:1.5px dashed #cfd3d9;border-radius:8px;display:flex;align-items:center;justify-content:center;font-size:40px;font-weight:300;color:#bbb}
.panel{position:absolute;left:927px;top:0;width:273px;height:871px;background:var(--panel)}
.panel-title{position:absolute;left:25px;top:33px;font-size:32px}
.learn{position:absolute;right:27px;top:46px;font-size:12px;color:var(--muted)}
.history{position:absolute;left:0;top:92px;width:273px;height:169px;background:linear-gradient(180deg,#6196f5,#4a7ce9)}
.history h3{position:absolute;left:24px;top:32px;font-size:17px;font-weight:400}
.history .for{position:absolute;right:11px;top:34px;font-size:12px;color:#d7e4ff}
.history .for b{color:var(--yellow);font-weight:400}
.bars{position:absolute;left:24px;top:60px}
.section-title{position:absolute;left:25px;font-size:17px}
.section-link{position:absolute;right:25px;font-size:12px;color:var(--muted)}
.cal{position:absolute;left:27px;top:333px;display:grid;grid-template-columns:repeat(7,25px);column-gap:6.7px;row-gap:7.5px}
.cal span{height:25px;display:flex;align-items:center;justify-content:center;font-size:12px;color:var(--soft);border-radius:2px;background:var(--cell)}
.cal .wd{background:none;height:16px;margin-bottom:5px}
.cal .dim{color:#6f7682}
.cal .y{background:var(--yellow);font-weight:700}
.cal .g{background:var(--green);font-weight:700;color:#fff}
.cal .p{background:var(--purple);font-weight:700;color:#fff}
.divider{position:absolute;left:0;top:540px;width:273px;height:1px;background:#30333a}
.trade{position:absolute;left:16px;width:240px;height:40px}
.coin{position:absolute;left:0;top:2px;width:36px;height:36px;border-radius:50%}
.trade .name{position:absolute;left:48px;top:3px;font-size:13.5px;font-style:italic}
.trade .tick{position:absolute;left:48px;top:22px;font-size:10px;color:var(--muted);font-style:italic}
.trade .status{position:absolute;left:128px;top:2px;font-size:13.5px;font-style:italic;color:var(--green)}
.trade .status.closed{color:var(--red)}
.trade .price{position:absolute;right:-2px;top:2px;font-size:13.5px;font-style:italic}
.trade .pct{position:absolute;right:3px;top:22px;font-size:8px;color:var(--green)}
.trade .pct.neg{color:var(--red)}
.chev{position:absolute;left:132px;top:846px}
</style>
</head>
<body>
<div class="app">
  <aside class="sidebar">
    <div class="avatar"></div>
    <div class="nav-active">
      <svg width="22" height="22" viewBox="0 0 22 22" fill="none" stroke="#fff" stroke-width="2.4"><rect x="2" y="2" width="6.5" height="6.5" rx="2"/><rect x="13.5" y="2" width="6.5" height="6.5" rx="2"/><rect x="2" y="13.5" width="6.5" height="6.5" rx="2"/><rect x="13.5" y="13.5" width="6.5" height="6.5" rx="2"/></svg>
    </div>
    <svg class="nav-icon" style="top:333px" viewBox="0 0 24 24" fill="none" stroke="#8a93a3" stroke-width="1.6"><path d="M3 21h18M6 18v-5M10 18V9M14 18v-7M18 18V4"/></svg>
    <div class="nav-sep" style="top:375px"></div>
    <svg class="nav-icon" style="top:384px" viewBox="0 0 24 24" fill="none" stroke="#8a93a3" stroke-width="1.6"><circle cx="9" cy="12" r="6"/><circle cx="15" cy="8" r="5"/><circle cx="17" cy="18" r="3"/></svg>
    <div class="nav-sep" style="top:435px"></div>
    <svg class="nav-icon" style="top:452px" viewBox="0 0 24 24" fill="none" stroke="#8a93a3" stroke-width="1.6"><path d="M3 4h15v11H8l-5 4z"/><path d="M18 8h3v12l-4-3H8"/></svg>
    <div class="nav-sep" style="top:495px"></div>
    <svg class="nav-icon" style="top:513px" viewBox="0 0 24 24" fill="none" stroke="#8a93a3" stroke-width="1.6"><rect x="3" y="5" width="18" height="16"/><path d="M3 10h18M8 2v5M16 2v5"/></svg>
    <div class="nav-sep" style="top:555px"></div>
    <svg class="nav-icon" style="top:574px" viewBox="0 0 24 24" fill="none" stroke="#8a93a3" stroke-width="1.6"><circle cx="12" cy="12" r="3.5"/><path d="M12 2l2 3 3.5-1 .5 3.5 3.5 1-1.5 3.5 1.5 3-3.5 1-.5 3.5-3.5-1L12 22l-2-3-3.5 1-.5-3.5-3.5-1L4 12 2.5 8.5 6 7.5 6.5 4 10 5z"/></svg>
    <div class="nav-sep" style="top:616px"></div>
    <svg class="nav-icon" style="top:633px" viewBox="0 0 24 24" fill="none" stroke="#8a93a3" stroke-width="1.6"><circle cx="12" cy="12" r="10"/><path d="M9.5 9.5a2.5 2.5 0 1 1 3.5 2.3c-.7.3-1 .9-1 1.7v.5"/><circle cx="12" cy="17" r=".6" fill="#8a93a3"/></svg>
    <div class="nav-sep" style="top:680px"></div>
    <div class="fab">+</div>
  </aside>

  <main>
    <div class="greeting">Good Morning Mira!</div>
    <h1 class="title">Dashboard<small>(Last Synced 09:14:67 a.m.)</small></h1>
    <div class="filter">Filter stats</div>
    <div class="filter-btn">
      <svg width="18" height="18" viewBox="0 0 18 18" fill="none" stroke="#9aa3b2" stroke-width="1.5"><rect x="1" y="2" width="16" height="6" rx="3"/><rect x="1" y="10" width="16" height="6" rx="3"/><circle cx="5" cy="5" r="1.6"/><circle cx="13" cy="13" r="1.6"/></svg>
    </div>

    <section class="chart-card">
      <div class="chart-title">p &amp; L Graph</div>
      <div class="range">from <b>August 2023 ▾</b> &nbsp; to <b>May 2024 ▾</b></div>
      <svg style="position:absolute;left:0;top:0" width="787" height="314" viewBox="0 0 787 314" fill="none">
        <g stroke="var(--grid)" stroke-width="1"><path d="M0 74H787M0 117H787M0 160H787M0 203H787M0 247H787"/></g>
        <path d="M63 180 C100 188,115 196,138 194 S190 176,214 175 S265 198,287 194 S330 150,357 149 S410 178,437 175 S485 143,505 143 S560 150,579 149 S630 132,648 136 S705 160,725 180" stroke="#4a4e55" stroke-width="1.5"/>
        <path d="M63 214 C100 192,120 176,142 178 S195 215,214 209 S260 136,287 139 S335 172,357 167 S405 136,430 138 S485 180,509 177 S550 142,579 142 S630 132,648 112 S665 110,669 125 S690 163,725 166" stroke="var(--line)" stroke-width="1.6"/>
        <circle cx="430" cy="138" r="12" fill="#5b8ff5" opacity=".18"/>
        <circle cx="430" cy="138" r="6" fill="#fff" stroke="#5b8ff5" stroke-width="3"/>
      </svg>
      <div class="tooltip">$400</div>
      <span class="axis" style="left:64px">Aug 2023</span>
      <span class="axis" style="left:137px">Sep 2023</span>
      <span class="axis" style="left:210px">Oct 2023</span>
      <span class="axis" style="left:284px">Nov 2023</span>
      <span class="axis" style="left:357px">Dec 2023</span>
      <span class="axis" style="left:430px">Jan 2024</span>
      <span class="axis" style="left:504px">Feb 2024</span>
      <span class="axis" style="left:577px">Mar 2024</span>
      <span class="axis" style="left:650px">Apr 2024</span>
      <span class="axis" style="left:723px">May 2024</span>
    </section>

    <div class="stat" style="left:103px;top:431px">
      <div class="value">$478.0</div>
      <div class="icon"><svg width="24" height="24" viewBox="0 0 24 24" fill="none" stroke="#fff" stroke-width="1.6"><circle cx="12" cy="12" r="10"/><path d="M15 9c-.5-1-1.6-1.5-3-1.5-1.8 0-3 .8-3 2s1.2 1.7 3 2 3 .8 3 2-1.2 2-3 2c-1.4 0-2.5-.5-3-1.5M12 6v12"/></svg></div>
      <div class="label">Total net Profit</div>
      <div class="sub"><span class="dot"></span>+3% Descrease than yesterday</div>
    </div>
    <div class="stat" style="left:375px;top:431px">
      <div class="value">$507.6</div>
      <div class="icon"><svg width="20" height="20" viewBox="0 0 20 20" fill="none" stroke="#fff" stroke-width="1.6"><rect x="3" y="2" width="14" height="16" rx="1"/><path d="M6 5h8v3H6zM6 11h1M10 11h1M14 11h0M6 14h1M10 14h1M13 11v3"/></svg></div>
      <div class="label">Average Win</div>
      <div class="sub"><span class="dot"></span>Daily</div>
    </div>
    <div class="stat" style="left:651px;top:431px">
      <div class="value">79%</div>
      <div class="icon"><svg width="22" height="22" viewBox="0 0 22 22" fill="none" stroke="#fff" stroke-width="2"><path d="M17 4L5 18"/><circle cx="6" cy="6" r="2.5"/><circle cx="16" cy="16" r="2.5"/></svg></div>
      <div class="label">Today Win Rate</div>
      <div class="sub"><span class="dot"></span>+3% Increase than yesterday</div>
    </div>
    <div class="stat red" style="left:103px;top:576px">
      <div class="value" style="top:35px">$31.0</div>
      <div class="icon" style="width:35px;height:35px;top:25px;right:24px"><svg width="18" height="18" viewBox="0 0 18 18" fill="none" stroke="#fff" stroke-width="1.6"><path d="M2 2v14h14M5 12l3-4 3 2 4-5"/></svg></div>
      <div class="label" style="top:85px">Today Fees &amp; Commissions</div>
      <div class="sub" style="top:100px">
        <span class="dot"></span>+3% Increase than yesterday</div>
    </div>
    <div class="stat blue" style="left:375px;top:576px">
      <div class="value" style="top:26px">6</div>
      <div class="icon"><svg width="20" height="20" viewBox="0 0 20 20" fill="#fff"><circle cx="13" cy="6" r="4"/><circle cx="5" cy="13" r="3"/><circle cx="13" cy="15" r="2.5"/></svg></div>
      <div class="label" style="top:78px">Trades</div>
      <div class="sub" style="top:96px"><span class="dot"></span>number of Ongoing Trades</div>
    </div>
    <div class="stat blue" style="left:651px;top:576px">
      <div class="value" style="top:26px">$19289.1</div>
      <div class="icon"><svg width="20" height="20" viewBox="0 0 20 20" fill="none" stroke="#fff" stroke-width="1.6"><rect x="4" y="4" width="12" height="12" rx="2"/></svg></div>
      <div class="label" style="top:78px">total Assets</div>
      <div class="sub" style="top:96px"><span class="dot"></span>wallet balance</div>
    </div>
    <div class="add-tile">+</div>
  </main>

  <aside class="panel">
    <div class="panel-title">Personal</div>
    <div class="learn">Learn more</div>
    <section class="history">
      <h3>History</h3>
      <div class="for">for <b>September 2023</b> ▾</div>
      <svg class="bars" width="225" height="80" viewBox="0 0 225 80" fill="rgba(255,255,255,.28)">
        <rect x="0" y="18" width="2.2" height="58"/><rect x="6.5" y="4" width="2.2" height="72"/><rect x="13" y="12" width="2.2" height="64"/><rect x="19.5" y="34" width="2.2" height="42"/><rect x="26" y="42" width="2.2" height="34"/><rect x="32.5" y="24" width="2.2" height="52"/><rect x="39" y="10" width="2.2" height="66"/><rect x="45.5" y="26" width="2.2" height="50"/><rect x="52" y="36" width="2.2" height="40"/><rect x="58.5" y="40" width="2.2" height="36"/><rect x="65" y="30" width="2.2" height="46"/><rect x="71.5" y="14" width="2.2" height="62"/><rect x="78" y="8" width="2.2" height="68"/><rect x="84.5" y="28" width="2.2" height="48"/><rect x="91" y="16" width="2.2" height="60"/><rect x="97.5" y="22" width="2.2" height="54"/><rect x="104" y="14" width="2.2" height="62"/><rect x="110.5" y="34" width="2.2" height="42"/><rect x="117" y="6" width="2.2" height="70"/><rect x="123.5" y="26" width="2.2" height="50"/><rect x="130" y="44" width="2.2" height="32"/><rect x="136.5" y="20" width="2.2" height="56"/><rect x="143" y="30" width="2.2" height="46"/><rect x="149.5" y="38" width="2.2" height="38"/><rect x="156" y="24" width="2.2" height="52"/><rect x="162.5" y="12" width="2.2" height="64"/><rect x="169" y="28" width="2.2" height="48"/><rect x="175.5" y="16" width="2.2" height="60"/><rect x="182" y="10" width="2.2" height="66"/><rect x="188.5" y="26" width="2.2" height="50"/><rect x="195" y="30" width="2.2" height="46"/><rect x="201.5" y="20" width="2.2" height="56"/><rect x="208" y="16" width="2.2" height="60"/><rect x="214.5" y="10" width="2.2" height="66"/><rect x="221" y="30" width="2.2" height="46"/>
      </svg>
    </section>

    <div class="section-title" style="top:289px">Calendar</div>
    <div class="section-link" style="top:293px;color:var(--text)">September 2023 ▾</div>
    <div class="cal">
      <span class="wd">S</span><span class="wd">M</span><span class="wd">T</span><span class="wd">W</span><span class="wd">T</span><span class="wd">F</span><span class="wd">S</span>
      <span class="dim">29</span><span class="dim">30</span><span class="dim">31</span><span>01</span><span class="y">02</span><span>03</span><span>04</span>
      <span>05</span><span>06</span><span>07</span><span>08</span><span>09</span><span>10</span><span>11</span>
      <span>12</span><span>13</span><span>14</span><span>15</span><span class="g">16</span><span class="g">17</span><span>18</span>
      <span>19</span><span class="p">20</span><span>21</span><span>22</span><span>23</span><span>24</span><span>25</span>
      <span>26</span><span>27</span><span>28</span><span>29</span><span>30</span><span>31</span><span class="dim">31</span>
    </div>
    <div class="divider"></div>

    <div class="section-title" style="top:565px">Ongoing Trades</div>
    <div class="section-link" style="top:569px">View all</div>

    <div class="trade" style="top:603px">
      <div class="coin" style="background:#f7931a"></div>
      <div class="name">Coinvale</div><div class="tick">CVL</div>
      <div class="status">Open</div>
      <div class="price">$4637.99</div><div class="pct">+9.77%</div>
    </div>
    <div class="trade" style="top:660px">
      <div class="coin" style="background:#6275d8"></div>
      <div class="name">Ethrix</div><div class="tick">ETX</div>
      <div class="status">Open</div>
      <div class="price">$4637.99</div><div class="pct neg">-1.13%</div>
    </div>
    <div class="trade" style="top:719px">
      <div class="coin" style="background:#e1141f"></div>
      <div class="name">Tronel</div><div class="tick">TRN</div>
      <div class="status closed">Closed</div>
      <div class="price">$4637.99</div><div class="pct neg">-3.34%</div>
    </div>
    <div class="trade" style="top:779px">
      <div class="coin" style="background:#f7931a"></div>
      <div class="name">Coinvale</div><div class="tick">CVL</div>
      <div class="status">Open</div>
      <div class="price">$4637.99</div><div class="pct">+9.77%</div>
    </div>
    <svg class="chev" width="14" height="10" viewBox="0 0 14 10" fill="none" stroke="#fff" stroke-width="1.6"><path d="M2 3l5 5 5-5"/></svg>
  </aside>
</div>
</body>
</html>
```